Brellwick Partners, LLC Stationary

Brellwick Partners, LLC is a new financial planning and consulting company. We are looking for designs on business cards, letterhead, envelopes, and anything else that would be useful. Our preference for business card design is two sided. We are looking for a professional and clean look with incorporating the logo and patriotic feel. Thank you to all who participate and good luck!

```html
<!DOCTYPE html>
<html lang="en">
<head>
<meta charset="utf-8">
<title>Brellwick Partners, LLC – Business Card</title>
<link rel="stylesheet" href="https://fonts.googleapis.com/css2?family=Montserrat:wght@400;600&display=swap">
<style>
  :root{
    --navy:#173d6b;
    --navy-deep:#0f2d52;
    --red:#c8202b;
    --red-deep:#8e1a22;
    --white:#ffffff;
    --page:#e9e6e1;
    --ink-soft:#dfe7f1;
  }
  *{margin:0;padding:0;box-sizing:border-box}
  html,body{width:1200px;height:950px;overflow:hidden;background:var(--page)}
  body{font-family:"Montserrat",Arial,sans-serif;display:flex;flex-direction:column;align-items:center;justify-content:center;gap:24px}
  .card{width:780px;height:446px;position:relative;overflow:hidden;border-radius:4px;box-shadow:0 6px 18px rgba(0,0,0,.18)}
  .card svg.card-art{position:absolute;inset:0;width:100%;height:100%}

  /* front */
  .card-front{background:var(--white)}
  .brand{position:absolute;left:52px;top:46px;display:flex;align-items:center;gap:14px;color:var(--navy)}
  .brand-dot{width:30px;height:30px;border-radius:50%;background:var(--red)}
  .brand-text{display:flex;flex-direction:column}
  .brand-name{font-weight:600;font-size:30px;letter-spacing:1px;line-height:1.1}
  .brand-tagline{font-weight:400;font-size:10px;letter-spacing:2.4px;text-transform:uppercase;margin-top:4px}
  .contact{position:absolute;right:42px;top:232px;text-align:right;color:var(--white)}
  .contact-name{font-weight:600;font-size:21px;letter-spacing:1px;text-transform:uppercase}
  .contact-role{font-size:15px;letter-spacing:1.5px;text-transform:uppercase;margin-bottom:10px}
  .contact-address{font-size:16px;line-height:1.4;margin-bottom:8px}
  .contact-line{font-size:16px;line-height:1.5;display:flex;justify-content:flex-end;align-items:center;gap:10px}
  .contact-icon{width:16px;height:16px;flex:none}

  /* back */
  .card-back{background:linear-gradient(135deg,var(--red) 0%,#b51d27 55%,var(--red-deep) 100%);color:var(--white)}
  .back-brand{position:absolute;left:0;right:0;top:150px;display:flex;justify-content:center;align-items:center;gap:18px}
  .back-brand .brand-dot{background:var(--white);width:40px;height:40px}
  .back-brand .brand-name{font-size:42px}
  .back-brand .brand-tagline{font-size:12px;letter-spacing:3px}
  .back-web{position:absolute;left:0;right:0;bottom:56px;text-align:center;font-size:18px;letter-spacing:3px}
</style>
</head>
<body>

<section class="card card-front" aria-label="Business card front">
  <svg class="card-art" viewBox="0 0 780 446" preserveAspectRatio="none" aria-hidden="true">
    <path d="M0 190 C150 170 230 300 360 300 C500 300 600 170 780 160 L780 446 L0 446 Z" fill="var(--red)"/>
    <path d="M0 206 C150 190 230 318 360 318 C500 318 600 186 780 176 L780 446 L0 446 Z" fill="var(--white)"/>
    <path d="M0 212 C150 200 230 326 360 326 C500 326 600 194 780 184 L780 446 L0 446 Z" fill="var(--navy)"/>
  </svg>

  <div class="brand">
    <span class="brand-dot"></span>
    <div class="brand-text">
      <span class="brand-name">BRELLWICK PARTNERS, LLC</span>
      <span class="brand-tagline">Financial Planning and Consulting</span>
    </div>
  </div>

  <div class="contact">
    <p class="contact-name">Nora Kessel</p>
    <p class="contact-role">President</p>
    <p class="contact-address">2716 Aldergate Lane<br>Marrow Bay, NY 11940</p>
    <p class="contact-line">555 0142 7781
      <svg class="contact-icon" viewBox="0 0 16 16"><path d="M4 2l2 3-1.5 1.5a8 8 0 0 0 5 5L11 10l3 2-1 2.5C7 15 1 9 1.5 3z" fill="currentColor"/></svg></p>
    <p class="contact-line">555 0198 3304
      <svg class="contact-icon" viewBox="0 0 16 16"><rect x="4" y="1.5" width="8" height="4" fill="currentColor"/><rect x="1.5" y="6" width="13" height="6" rx="1" fill="currentColor"/><rect x="4" y="10" width="8" height="4.5" fill="var(--navy)" stroke="currentColor"/></svg></p>
    <p class="contact-line">nora@brellwick.com
      <svg class="contact-icon" viewBox="0 0 16 16"><rect x="1.5" y="3.5" width="13" height="9" fill="currentColor"/><path d="M1.5 3.5L8 9l6.5-5.5" fill="none" stroke="var(--navy)" stroke-width="1.2"/></svg></p>
    <p class="contact-line">www.brellwick.com
      <svg class="contact-icon" viewBox="0 0 16 16"><circle cx="8" cy="8" r="6.5" fill="currentColor"/><path d="M1.5 8h13M8 1.5c-3 3-3 10 0 13M8 1.5c3 3 3 10 0 13" fill="none" stroke="var(--navy)" stroke-width="1"/></svg></p>
  </div>
</section>

<section class="card card-back" aria-label="Business card back">
  <div class="back-brand">
    <span class="brand-dot"></span>
    <div class="brand-text">
      <span class="brand-name">BRELLWICK PARTNERS, LLC</span>
      <span class="brand-tagline">Financial Planning and Consulting</span>
    </div>
  </div>
  <p class="back-web">www.brellwick.com</p>
</section>

</body>
</html>
```